Email design required

We need a design for a paid B2B email campaign and facebook / retargeting banner ads that match the same style.

Website: http://pelmora.staging.hostvantry.com/
Campaign Name: KEX Weariness
Example: http://liftmarrowsites.com/kex-weariness/
- I made this over the weekend. It has the right words, but the style / layout needs to change

Size: 600 pixels wide, no limit on length

Formatting:
Format CSS inline only - This will ensure that size, font family, colour, line height, etc. will all remain the same once it is dropped into our newsletter sending software. See below as an

example,

Here's a mockup of

Target Market(s)

Canadian mortgage brokers

Industry/Entity Type

Campaign

Font styles to use
Sans Serif

Colors
3277b5

Requirements
Must have
• Text from my website example http://liftmarrowsites.com/kex-weariness/
• Otherwise, do whatever you think would look good.

```html
<!DOCTYPE html>
<html lang="en">
<head>
<meta charset="utf-8">
<title>KEX Weariness – Compare Table Styles</title>
<link href="https://fonts.googleapis.com/css2?family=Open+Sans:ital,wght@0,400;0,600;0,700;1,400&display=swap" rel="stylesheet">
<style>
:root{
  --board-dark:#2a2a2a;
  --board-mid:#3a3a3a;
  --heading-grey:#8d8d8d;
  --style-green:#b4f01c;
  --brand-blue:#3277b5;
  --logo-blue:#1e5fa8;
  --row-bright:#0a85dc;
  --row-navy:#013f7e;
  --row-light-a:#e4eff9;
  --row-light-b:#d5e8f8;
  --text-dark:#2b2b2b;
  --check-teal:#16b8a4;
  --cta-orange:#f7931e;
  --white:#ffffff;
}
*{box-sizing:border-box;margin:0;padding:0}
html,body{width:1200px;height:1200px;overflow:hidden}
body{font-family:"Open Sans",Arial,sans-serif;color:var(--text-dark)}
.board{position:relative;width:1200px;height:1200px;
  background:radial-gradient(ellipse at 50% 40%,var(--board-mid),var(--board-dark) 75%);}
.board-title{position:absolute;left:0;width:1200px;text-align:center;color:var(--heading-grey);
  font-weight:700;font-size:24px;letter-spacing:.3px}
.board-title.line-1{top:12px}
.board-title.line-2{top:54px}
.style-label{position:absolute;width:480px;text-align:center;color:var(--style-green);
  font-weight:700;font-size:26px}
.card{position:absolute;width:480px;background:var(--white);padding-top:11px}
.card-header{background:var(--brand-blue);color:var(--white);height:39px;line-height:39px;
  text-align:center;font-weight:600;font-size:14px}
.brand-row{position:relative;height:58px}
.brand{position:absolute;top:20px;display:flex;align-items:center;gap:4px;
  color:var(--logo-blue);font-weight:600;font-size:18px}
.brand-mark{width:13px;height:13px;border:2px solid var(--logo-blue)}
.rival{position:absolute;top:24px;font-weight:600;font-size:12.5px;color:var(--text-dark)}
.compare{position:absolute;left:34px;width:403px;font-size:11px}
.row{position:relative;height:27px;line-height:27px}
.row .icon{position:absolute;left:5px;top:7px;width:12px;height:12px}
.row .label{position:absolute;left:26px}
.row .ours,.row .theirs{position:absolute;width:120px;margin-left:-60px;text-align:center}
.row .ours{left:var(--ours-x);font-weight:600}
.row .theirs{left:var(--theirs-x)}
.row .tick{position:absolute;left:var(--ours-x);margin-left:-9px;top:5px;width:18px;height:16px}
.row.tall{height:79px}
.row .detail{position:absolute;left:26px;top:22px;font-style:italic;font-size:10px;line-height:17px;width:180px}
.dark .row{color:var(--white)}
.dark .row:nth-child(odd){background:var(--row-bright)}
.dark .row:nth-child(even){background:var(--row-navy)}
.light .row:nth-child(odd){background:var(--row-light-a)}
.light .row:nth-child(even){background:var(--row-light-b)}
.light .row.sub{background:var(--row-light-b)}
.light .row.sub .label{left:34px}
.light .row.blank{background:var(--white)}
.lined .row.sub{border-top:2px solid var(--white);font-style:italic}
.row.sub.double{height:36px;line-height:13px}
.row.sub.double .label{top:6px}
.row.sub.double .tick{top:8px}
.row.sub.double .theirs{line-height:36px}
.cta{position:absolute;width:254px;height:60px;margin-left:-127px;left:240px;
  background:var(--cta-orange);border-radius:30px;color:var(--white);text-align:center}
.cta-main{display:block;font-weight:700;font-size:19px;letter-spacing:.8px;padding-top:8px;line-height:24px}
.cta-sub{display:block;font-weight:700;font-size:11px;letter-spacing:.3px}
</style>
</head>
<body>
<svg width="0" height="0" style="position:absolute">
  <defs>
    <symbol id="icon-check-circle" viewBox="0 0 12 12">
      <circle cx="6" cy="6" r="4.6" fill="none" stroke="currentColor" stroke-width="1.4" stroke-dasharray="22 6"/>
      <path d="M3.6 6l1.8 1.8L10.5 2.8" fill="none" stroke="currentColor" stroke-width="1.5"/>
    </symbol>
    <symbol id="icon-tick-box" viewBox="0 0 18 16">
      <path d="M1.5 3.5v11h12V9" fill="none" stroke="#2d6fa6" stroke-width="1.6"/>
      <path d="M4 7l3.5 3.5L17 1.5" fill="none" stroke="var(--check-teal)" stroke-width="2.4"/>
    </symbol>
  </defs>
</svg>

<main class="board">
  <div class="board-title line-1">DESIGN IDEAS of various Individual Elements</div>
  <div class="board-title line-2">CLIENT Changes To Design &nbsp;# 11527444</div>

  <div class="style-label" style="left:43px;top:158px">Dark TABLE Style - 01</div>
  <div class="style-label" style="left:650px;top:158px">Light TABLE Style - 02</div>
  <div class="style-label" style="left:43px;top:667px">Light TABLE Style - 03</div>
  <div class="style-label" style="left:650px;top:667px">Light TABLE Style - 04</div>

  <!-- Style 01 -->
  <section class="card" style="left:36px;top:230px;height:362px">
    <div class="card-header">Compare KEX Services</div>
    <div class="brand-row">
      <div class="brand" style="left:232px"><span class="brand-mark"></span>Pelmora</div>
      <div class="rival" style="left:361px">‘Other Guys’</div>
    </div>
    <div class="compare dark" style="top:109px;--ours-x:242px;--theirs-x:358px">
      <div class="row"><svg class="icon" style="color:#fff"><use href="#icon-check-circle"/></svg><span class="label">Price</span><span class="ours">$29 / month</span><span class="theirs">$39 / Order</span></div>
      <div class="row"><svg class="icon" style="color:#fff"><use href="#icon-check-circle"/></svg><span class="label">Units</span><span class="ours">Unlimited</span><span class="theirs">Just One</span></div>
      <div class="row"><svg class="icon" style="color:#fff"><use href="#icon-check-circle"/></svg><span class="label">Turnaround</span><span class="ours">4 Hours</span><span class="theirs">1 Day</span></div>
      <div class="row tall"><svg class="icon" style="color:#fff"><use href="#icon-check-circle"/></svg><span class="label">Other Services</span><svg class="tick"><use href="#icon-tick-box"/></svg><span class="theirs">X</span>
        <span class="detail">Document Sorting, Lender Fulfillment, Closing Package Preparation, And Much More</span></div>
    </div>
    <div class="cta" style="top:285px"><span class="cta-main">GET STARTED NOW</span><span class="cta-sub">30-Day Money Back Guarantee</span></div>
  </section>

  <!-- Style 02 -->
  <section class="card" style="left:661px;top:230px;height:362px">
    <div class="card-header">Compare KEX Services</div>
    <div class="brand-row">
      <div class="brand" style="left:232px"><span class="brand-mark"></span>Pelmora</div>
      <div class="rival" style="left:361px">‘Other Guys’</div>
    </div>
    <div class="compare light" style="top:109px;--ours-x:242px;--theirs-x:358px">
      <div class="row"><svg class="icon" style="color:#9a9a9a"><use href="#icon-check-circle"/></svg><span class="label">Price</span><span class="ours">$29 / month</span><span class="theirs">$39 / Order</span></div>
      <div class="row"><svg class="icon" style="color:#9a9a9a"><use href="#icon-check-circle"/></svg><span class="label">Units</span><span class="ours">Unlimited</span><span class="theirs">Just One</span></div>
      <div class="row"><svg class="icon" style="color:#9a9a9a"><use href="#icon-check-circle"/></svg><span class="label">Turnaround</span><span class="ours">4 Hours</span><span class="theirs">1 Day</span></div>
      <div class="row tall"><svg class="icon" style="color:#9a9a9a"><use href="#icon-check-circle"/></svg><span class="label">Other Services</span><svg class="tick"><use href="#icon-tick-box"/></svg><span class="theirs">X</span>
        <span class="detail">Document Sorting, Lender Fulfillment, Closing Package Preparation, And Much More</span></div>
    </div>
    <div class="cta" style="top:285px"><span class="cta-main">GET STARTED NOW</span><span class="cta-sub">30-Day Money Back Guarantee</span></div>
  </section>

  <!-- Style 03 -->
  <section class="card" style="left:34px;top:728px;height:420px">
    <div class="card-header">Compare KEX Services</div>
    <div class="brand-row">
      <div class="brand" style="left:210px"><span class="brand-mark"></span>Pelmora</div>
      <div class="rival" style="left:351px">‘Other Guys’</div>
    </div>
    <div class="compare light" style="top:114px;--ours-x:220px;--theirs-x:350px">
      <div class="row"><svg class="icon" style="color:#9a9a9a"><use href="#icon-check-circle"/></svg><span class="label">Price</span><span class="ours">$29 / month</span><span class="theirs">$39 / Order</span></div>
      <div class="row"><svg class="icon" style="color:#9a9a9a"><use href="#icon-check-circle"/></svg><span class="label">Units</span><span class="ours">Unlimited</span><span class="theirs">Just One</span></div>
      <div class="row"><svg class="icon" style="color:#9a9a9a"><use href="#icon-check-circle"/></svg><span class="label">Turnaround</span><span class="ours">4 Hours</span><span class="theirs">1 Day</span></div>
      <div class="row"><svg class="icon" style="color:#9a9a9a"><use href="#icon-check-circle"/></svg><span class="label">Other Services</span><span class="ours">Several</span><span class="theirs">X</span></div>
      <div class="row sub"><span class="label">Document Sorting</span><svg class="tick"><use href="#icon-tick-box"/></svg><span class="theirs">X</span></div>
      <div class="row sub"><span class="label">Lender Fulfillment</span><svg class="tick"><use href="#icon-tick-box"/></svg><span class="theirs">X</span></div>
      <div class="row sub double" style="height:43px"><span class="label">Closing Package Prepartion<br>And Much More</span><svg class="tick"><use href="#icon-tick-box"/></svg><span class="theirs">X</span></div>
    </div>
    <div class="cta" style="top:338px"><span class="cta-main">GET STARTED NOW</span><span class="cta-sub">30-Day Money Back Guarantee</span></div>
  </section>

  <!-- Style 04 -->
  <section class="card" style="left:659px;top:726px;height:420px">
    <div class="card-header">Compare KEX Services</div>
    <div class="brand-row">
      <div class="brand" style="left:212px"><span class="brand-mark"></span>Pelmora</div>
      <div class="rival" style="left:364px">‘Other Guys’</div>
    </div>
    <div class="compare light lined" style="top:114px;--ours-x:222px;--theirs-x:364px">
      <div class="row"><svg class="icon" style="color:#9a9a9a"><use href="#icon-check-circle"/></svg><span class="label">Price</span><span class="ours">$29 / month</span><span class="theirs">$39 / Order</span></div>
      <div class="row"><svg class="icon" style="color:#9a9a9a"><use href="#icon-check-circle"/></svg><span class="label">Units</span><span class="ours">Unlimited</span><span class="theirs">Just One</span></div>
      <div class="row"><svg class="icon" style="color:#9a9a9a"><use href="#icon-check-circle"/></svg><span class="label">Turnaround</span><span class="ours">4 Hours</span><span class="theirs">1 Day</span></div>
      <div class="row blank" style="height:29px"><svg class="icon" style="color:#9a9a9a"><use href="#icon-check-circle"/></svg><span class="label">Other Services</span></div>
      <div class="row sub"><span class="label">Document Sorting</span><svg class="tick"><use href="#icon-tick-box"/></svg><span class="theirs" style="font-style:normal">X</span></div>
      <div class="row sub"><span class="label">Lender Fulfillment</span><svg class="tick"><use href="#icon-tick-box"/></svg><span class="theirs" style="font-style:normal">X</span></div>
      <div class="row sub double"><span class="label">Closing Package Prepartion<br>And Much More</span><svg class="tick"><use href="#icon-tick-box"/></svg><span class="theirs" style="font-style:normal">X</span></div>
    </div>
    <div class="cta" style="top:338px"><span class="cta-main">GET STARTED NOW</span><span class="cta-sub">30-Day Money Back Guarantee</span></div>
  </section>
</main>
</body>
</html>
```